Rack Card for Charter Sail Boat business in SF Bay

We are in need of a rack card design to highlight the business to tourists and locals. 2 sided card 3.86" x 8.39" (full bleed)

We are looking for visually appleaing designs on the front and back but a little more detail on the back.

Use the info provided (text and info) on the website to include the 3 key services (Quick, 1/2 day, fullday) and aspects of the boat, location and other key info for customers (not prices). DO NOT INCLUDE ALL THIS TEXT please pick the elements you would like to fit your design and inform the customer as you would like about the business.

I can also provide photos directly from the video if you think those would fit your design. If video doesn't work on this upload you can view it at the website or facebook page (www.fb.com/tidewrenmarinellc)

Target Market(s)

Tourists and locals to san francisco east bay. 25 - 55 years old. Men and women.

Industry/Entity Type

Entertainment

Colors
0455a3
ec1f27
f3f1f8

Requirements
Must have
• Highlight services, key contact information (email, phone, website site), Visual impact
• 2-sided card - 3.86" x 8.39" (98 x 213 mm)
Nice to have
• facebook link, electric engine(green),

```html
<!DOCTYPE html>
<html lang="en">
<head>
<meta charset="utf-8">
<title>Tidewren Marine Rack Card</title>
<link href="https://fonts.googleapis.com/css2?family=Oswald:wght@500;600&family=Roboto:wght@400;500;700&display=swap" rel="stylesheet">
<style>
:root{
  --blue:#0455a3;
  --red:#ec1f27;
  --paper:#f3f1f8;
  --white:#ffffff;
  --yellow:#f7e04b;
  --ink:#4a4f57;
  --stage:#d9dadc;
  --green:#5dbb46;
}
*{margin:0;padding:0;box-sizing:border-box}
html,body{width:1200px;height:1200px;overflow:hidden}
body{background:var(--stage);font-family:"Roboto",Arial,sans-serif;position:relative}
.card{position:absolute;top:100px;width:460px;height:1000px;background:var(--white);overflow:hidden;box-shadow:0 6px 18px rgba(0,0,0,.18)}
.card--front{left:110px}
.card--back{left:630px}
.photo{position:absolute}
.panel{position:absolute;color:var(--white);padding:12px 14px;overflow:hidden}
.panel--red{background:var(--red)}
.panel--blue{background:var(--blue)}
.panel h3{font-family:"Oswald",Arial,sans-serif;font-weight:600;font-size:15px;line-height:1.2;text-transform:uppercase;margin-bottom:5px;letter-spacing:.2px}
.panel p{font-size:10.5px;line-height:1.3}
.card--back .panel h3{color:var(--yellow);font-size:17px}
.card--back .panel--trip h3{color:var(--white);font-size:13px}
.card--back .panel--trip p{font-size:10px;line-height:1.3}
.brand{position:absolute;left:0;top:0;width:460px;height:135px;display:flex;align-items:center;justify-content:center;gap:12px}
.brand__dot{width:22px;height:22px;border-radius:50%;background:var(--red)}
.brand__name{font-family:"Oswald",Arial,sans-serif;font-weight:500;font-size:40px;color:var(--blue);letter-spacing:1px}
.hero{position:absolute;left:30px;top:135px;width:200px;height:250px;background:var(--red);color:var(--white);padding:26px 16px;font-family:"Oswald",Arial,sans-serif;font-weight:500;font-size:22px;line-height:1.35;text-align:center;z-index:2}
.footer{position:absolute;left:0;width:460px;color:var(--ink)}
.contact{display:flex;align-items:center;gap:7px;font-family:"Oswald",Arial,sans-serif;font-weight:500;font-size:15px;white-space:nowrap}
.contact--phone{color:var(--red)}
.contact--mail{color:var(--blue)}
.contact--web,.contact--social{color:var(--ink);font-size:13px}
.contact svg{flex:none}
.social-mark{width:16px;height:16px;border-radius:50%;border:1.5px solid var(--ink)}
.footer-band{position:absolute;left:0;bottom:0;width:460px;height:10px;background:var(--paper)}
.footer-band--green{background:var(--green);height:4px}
.badge{position:absolute;right:24px;width:70px;height:70px;border-radius:50%;background:var(--blue);border:3px solid var(--yellow)}
</style>
</head>
<body>

<section class="card card--front">
  <div class="brand">
    <span class="brand__dot"></span>
    <span class="brand__name">Tidewren Marine</span>
  </div>

  <div class="photo" style="left:215px;top:95px;width:245px;height:280px;background:linear-gradient(160deg,#2e6fc4 0%,#6fa6dc 45%,#e4e8ee 70%,#7b8794 100%)" role="img" aria-label="Photo of the sailboat deck and sails under a blue sky"></div>

  <div class="hero">Enjoy an amazing experience aboard Tidewren and view San Francisco and the rest of the bay</div>

  <div class="photo" style="left:0;top:385px;width:215px;height:185px;background:linear-gradient(180deg,#5c9ad8 0%,#9bc1e6 40%,#2f4f6e 55%,#2d6fb3 75%,#7fb0de 100%)" role="img" aria-label="Photo of sunlight sparkling on the bay with hills beyond"></div>

  <div class="panel panel--blue" style="left:215px;top:370px;width:245px;height:165px">
    <h3>Modern</h3>
    <p>Tidewren is completely electric which means no diesel smells, noise or vibration to suffer. New electrics, plumbing, toilets, and deck areas compliment the elegant lines and features of this Harlow Pierce 46 foot cutter rigged sailboat.</p>
  </div>

  <div class="panel panel--blue" style="left:0;top:570px;width:230px;height:285px">
    <h3>Entertaining</h3>
    <p>Surrounded by the beauty and wonder of the San Francisco Bay you will enjoy the choice of sounds from your source, StarWave radio, CD or old school FM! You can take the helm to experience the thrill of sailing Tidewren while we explore Alcatraz and Angel Islands, the Golden Gate and Bay Bridges, the City front or the many other hidden gems. While taking it all in, you and your guests can enjoy refreshments and snacks we provide or even choose to have lunch or dinner at anchor or on a private beach!</p>
  </div>

  <div class="photo" style="left:230px;top:535px;width:140px;height:135px;background:linear-gradient(150deg,#c9d3dc 0%,#5a6b7c 50%,#2e4a78 100%)" role="img" aria-label="Photo of young guests in life jackets at the helm"></div>
  <div class="photo" style="left:370px;top:535px;width:90px;height:135px;background:linear-gradient(180deg,#6fa3d9 0%,#b9cfe3 55%,#3b5a78 100%)" role="img" aria-label="Photo of sailboats moored in the marina"></div>

  <div class="panel panel--red" style="left:230px;top:670px;width:230px;height:185px">
    <h3>Safe</h3>
    <p>We carry aboard everything to make your time aboard safe. Life preservers are of course provided and available for all including kids sizes. We carry the USCG bulky ones as well as modern self inflating slim comfortable life jackets. Also loaded for every trip is a complete first aid kit, AED, EPIRB, and many other safety items.</p>
  </div>

  <div class="footer" style="top:864px;padding:0 14px 0 240px">
    <div class="contact contact--mail" style="font-size:14px">
      <svg width="20" height="14" viewBox="0 0 20 14"><rect x="1" y="1" width="18" height="12" fill="none" stroke="var(--blue)" stroke-width="1.6"/><polyline points="1,1 10,8 19,1" fill="none" stroke="var(--blue)" stroke-width="1.6"/></svg>
      Bookings@TidewrenMarine.com
    </div>
  </div>

  <div class="footer" style="top:905px;padding:0 30px">
    <div class="contact contact--phone">
      <svg width="18" height="18" viewBox="0 0 18 18"><circle cx="9" cy="9" r="8" fill="none" stroke="var(--red)" stroke-width="1.6"/><path d="M6 5.2l1.4-.6 1.1 2.2-.9.8c.4 1 1.1 1.7 2 2.1l.8-.9 2.2 1.1-.6 1.4c-3 .3-6.3-3-6-6.1z" fill="var(--red)"/></svg>
      +1(555) 014 WIND (9463)
    </div>
    <div style="display:flex;gap:26px;margin-top:14px;padding-left:56px">
      <div class="contact contact--web">
        <svg width="16" height="16" viewBox="0 0 16 16"><circle cx="8" cy="8" r="7" fill="none" stroke="var(--ink)" stroke-width="1.4"/><ellipse cx="8" cy="8" rx="3" ry="7" fill="none" stroke="var(--ink)" stroke-width="1.2"/><line x1="1" y1="8" x2="15" y2="8" stroke="var(--ink)" stroke-width="1.2"/></svg>
        www.tidewrenmarine.com
      </div>
      <div class="contact contact--social"><span class="social-mark"></span>/tidewrenmarinellc</div>
    </div>
  </div>
  <div class="footer-band"></div>
</section>

<section class="card card--back">
  <div class="panel panel--blue panel--trip" style="left:0;top:0;width:460px;height:125px">
    <h3>The Trip</h3>
    <p>When chartering Tidewren, the vessel is yours to direct anywhere within the time you wish to enjoy her. We do have a few old favorites that are always fun that we have listed below. These are just to provide an idea of the possible cruise as every trip takes into account your ideas and natures (tides, weather and currents) will. If your looking for something a little different or to mix it up a bit, let us know and we can make it happen. Our custom trips are simple to arrange and book, we simply ask for a minimum of 3 hours duration.</p>
  </div>

  <div class="panel panel--red" style="left:0;top:125px;width:230px;height:125px">
    <h3>2 Hour Blast</h3>
    <p>Could be a sunset sail, an early morning wake up cruise or a blast out into the bay anytime to find peace, fresh air and amazing views.</p>
  </div>
  <div class="photo" style="left:230px;top:125px;width:230px;height:125px;background:linear-gradient(120deg,#aacbe8 0%,#c9dcee 55%,#e3e6d8 100%)" role="img" aria-label="Map of the bay showing the two hour route"></div>

  <div class="photo" style="left:0;top:250px;width:255px;height:125px;background:linear-gradient(120deg,#d9e2cf 0%,#aacbe8 35%,#c9dcee 100%)" role="img" aria-label="Map of the bay showing the half day route"></div>
  <div class="panel panel--blue" style="left:255px;top:250px;width:205px;height:125px">
    <h3>½ Day Fun</h3>
    <p>A full morning, afternoon or evening out in the Bay seeing many of the main features and landmarks close to the Bay from the water. Actual duration 4-5 hours</p>
  </div>

  <div class="panel panel--red" style="left:0;top:375px;width:240px;height:125px">
    <h3>Full Day Adventure</h3>
    <p>The day includes a complete circuit of the Bay and lunch at anchor. Actual duration 7-8 hours</p>
  </div>
  <div class="photo" style="left:240px;top:375px;width:220px;height:125px;background:linear-gradient(120deg,#aacbe8 0%,#d9e2cf 60%,#e3e6d8 100%)" role="img" aria-label="Map of the bay showing the full day circuit"></div>

  <div class="photo" style="left:0;top:500px;width:460px;height:340px;background:linear-gradient(180deg,#8fb2cf 0%,#c9b98a 38%,#f0c870 48%,#5a6f82 62%,#2e3c4a 100%)" role="img" aria-label="Photo of the sailboat deck at sunset over the bay"></div>
  <div class="badge" style="top:526px"></div>

  <div class="footer" style="top:860px;padding:0 20px;display:flex;justify-content:space-between;align-items:center">
    <div class="contact contact--phone" style="font-size:14px">
      <svg width="18" height="18" viewBox="0 0 18 18"><circle cx="9" cy="9" r="8" fill="none" stroke="var(--red)" stroke-width="1.6"/><path d="M6 5.2l1.4-.6 1.1 2.2-.9.8c.4 1 1.1 1.7 2 2.1l.8-.9 2.2 1.1-.6 1.4c-3 .3-6.3-3-6-6.1z" fill="var(--red)"/></svg>
      +1(555) 014 WIND (9463)
    </div>
    <div class="contact contact--mail" style="font-size:13.5px">
      <svg width="20" height="14" viewBox="0 0 20 14"><rect x="1" y="1" width="18" height="12" fill="none" stroke="var(--blue)" stroke-width="1.6"/><polyline points="1,1 10,8 19,1" fill="none" stroke="var(--blue)" stroke-width="1.6"/></svg>
      Bookings@TidewrenMarine.com
    </div>
  </div>
  <div class="footer" style="top:905px;padding:0 40px;display:flex;gap:26px">
    <div class="contact contact--web">
      <svg width="16" height="16" viewBox="0 0 16 16"><circle cx="8" cy="8" r="7" fill="none" stroke="var(--ink)" stroke-width="1.4"/><ellipse cx="8" cy="8" rx="3" ry="7" fill="none" stroke="var(--ink)" stroke-width="1.2"/><line x1="1" y1="8" x2="15" y2="8" stroke="var(--ink)" stroke-width="1.2"/></svg>
      www.tidewrenmarine.com
    </div>
    <div class="contact contact--social"><span class="social-mark"></span>/tidewrenmarinellc</div>
  </div>
  <div class="footer-band footer-band--green"></div>
</section>

</body>
</html>
```